Vantro cards

I am in the auto motive, transportation business I would like a business card that is Something cool, modern edgy, having to do with car culture. I offer towing service for high and exotic cars. I also provide towing for collisions and car accidents. I offer open and enclosed transport nationwide.

Target Market(s)

Car culture people high end auto collectors

Industry/Entity Type

Towing car carrier

Contact Information for Business Card

My company colors black yellow and silver

Font styles to use
Serif

```html
<!DOCTYPE html>
<html lang="en">
<head>
<meta charset="utf-8">
<title>Vantro Transportation – Business Cards</title>
<link href="https://fonts.googleapis.com/css2?family=Montserrat:wght@400;600;800&display=swap" rel="stylesheet">
<style>
  :root {
    --stage: #cfc8bd;
    --card-white: #ffffff;
    --card-black: #1b1b1b;
    --brand-yellow: #f9dc5c;
    --ink: #1e1e1e;
    --silver: #8a8c90;
    --shadow: rgba(0, 0, 0, 0.45);
  }
  * { margin: 0; padding: 0; box-sizing: border-box; }
  html, body {
    width: 900px; height: 1200px; overflow: hidden;
    background: var(--stage);
    font-family: "Montserrat", sans-serif;
  }
  .canvas { position: relative; width: 900px; height: 1200px; }

  .card {
    position: absolute; left: 80px; width: 742px; height: 440px;
    border-radius: 40px; overflow: hidden;
    box-shadow: 0 4px 10px var(--shadow);
  }
  .card--front { top: 132px; background: var(--card-white); }
  .card--back { top: 638px; background: var(--card-black); }

  /* front */
  .brand-mark {
    position: absolute; left: 70px; top: 150px; width: 225px;
    text-align: center; color: var(--ink);
    font-weight: 800; text-transform: uppercase; line-height: 1.05;
  }
  .brand-mark__name { font-size: 46px; letter-spacing: 1px; }
  .brand-mark__sub { font-size: 17px; letter-spacing: 1.5px; }

  .divider {
    position: absolute; left: 346px; top: 125px;
    width: 2px; height: 214px; background: var(--brand-yellow);
  }
  .contact { position: absolute; left: 401px; top: 120px; color: var(--ink); }
  .contact__name { font-size: 26px; font-weight: 600; color: var(--brand-yellow); line-height: 1.2; }
  .contact__role { font-size: 16px; margin-top: 2px; }
  .contact__list { list-style: none; margin-top: 26px; font-size: 16px; line-height: 21px; }
  .contact__list li { display: flex; align-items: center; gap: 9px; }
  .contact__list svg { width: 15px; height: 12px; fill: var(--ink); flex: none; }
  .contact__address { margin-top: 22px; font-size: 16px; line-height: 20px; font-style: normal; }

  /* back */
  .vehicle-art {
    position: absolute; left: 350px; top: 20px; width: 392px; height: 400px;
    background: linear-gradient(100deg, #1b1b1b 0%, #2a2a2b 40%, #4a4b4e 85%, #5e5f62 100%);
  }
  .brand-mark--back {
    left: 221px; top: 170px; width: 300px; color: var(--card-white);
  }
  .brand-mark--back .brand-mark__name { font-size: 60px; }
  .brand-mark--back .brand-mark__sub { font-size: 22px; }
  .back-stripe {
    position: absolute; left: 0; bottom: 0; width: 100%; height: 10px;
    background: var(--brand-yellow);
  }
</style>
</head>
<body>
<div class="canvas">

  <section class="card card--front">
    <div class="brand-mark">
      <div class="brand-mark__name">Vantro</div>
      <div class="brand-mark__sub">Transportation</div>
    </div>

    <div class="divider"></div>

    <div class="contact">
      <div class="contact__name">Daniel Hart</div>
      <div class="contact__role">Owner</div>
      <ul class="contact__list">
        <li><svg viewBox="0 0 15 12"><path d="M1 4c0-2 3-3 6.5-3S14 2 14 4v1h-3V4H4v1H1z"/><rect x="2" y="6" width="11" height="6" rx="1"/></svg>(555) 214-7390</li>
        <li><svg viewBox="0 0 15 12"><path d="M0 1h15v1L7.5 7 0 2z"/><path d="M0 3.5l7.5 5 7.5-5V11H0z"/></svg>info@vantrotransportation.com</li>
        <li><svg viewBox="0 0 15 12"><circle cx="7.5" cy="6" r="5.5"/></svg>www.vantrotransportation.com</li>
      </ul>
      <address class="contact__address">48 Elm Street<br>Marlow, PA 17000</address>
    </div>
  </section>

  <section class="card card--back">
    <div class="vehicle-art" role="img" aria-label="Large dark silhouette of a truck front fading into the card"></div>
    <div class="brand-mark brand-mark--back">
      <div class="brand-mark__name">Vantro</div>
      <div class="brand-mark__sub">Transportation</div>
    </div>
    <div class="back-stripe"></div>
  </section>

</div>
</body>
</html>
```